Business card for medical clinic

I need an upmarket, modern medical/health business card for my clinic

Contact Information for Business Card

name, address, email, qr code

```html
<!DOCTYPE html>
<html lang="en">
<head>
<meta charset="utf-8">
<title>Meridan Care Partners – Business Card</title>
<link href="https://fonts.googleapis.com/css2?family=Cinzel:wght@500&family=Arimo:wght@400&display=swap" rel="stylesheet">
<style>
  :root{
    --backdrop:#3d3d3d;
    --card-dark:#2d2d2f;
    --card-light:#ffffff;
    --brand-blue:#1a6fa8;
    --accent-cyan:#16a4e4;
    --text-light:#f2f2f2;
    --text-muted:#d8d8d8;
  }
  *{box-sizing:border-box;margin:0;padding:0}
  html,body{width:1200px;height:803px;overflow:hidden;background:var(--backdrop)}
  .canvas{position:relative;width:1200px;height:803px}
  .card{position:absolute;top:250px;width:520px;height:300px;border-radius:18px;overflow:hidden}
  .card--front{left:40px;background:var(--card-dark)}
  .card--back{left:640px;background:var(--card-light)}

  .brand{display:flex;align-items:center;gap:10px;font-family:'Cinzel',serif;font-weight:500;color:var(--brand-blue);letter-spacing:.04em;white-space:nowrap}
  .brand__dot{flex:none;border-radius:50%;background:var(--brand-blue)}

  .front__brand{position:absolute;left:36px;top:36px;font-size:17px}
  .front__brand .brand__dot{width:10px;height:10px}
  .front__rule{position:absolute;left:36px;top:66px;width:200px;height:1px;background:var(--brand-blue)}

  .person{position:absolute;left:36px;top:92px}
  .person__name{font-family:'Cinzel',serif;font-weight:500;font-size:22px;color:var(--brand-blue);letter-spacing:.05em}
  .person__role{font-family:'Arimo',sans-serif;font-size:12px;color:var(--text-muted);margin-top:2px}

  .address{position:absolute;left:36px;top:150px;font-family:'Arimo',sans-serif;font-size:12.5px;line-height:1.4;color:var(--text-light)}

  .contacts{position:absolute;left:36px;top:196px;list-style:none;font-family:'Arimo',sans-serif;font-size:12.5px;color:var(--text-light)}
  .contacts li{display:flex;align-items:center;gap:8px;height:19px}
  .contacts svg{width:11px;height:11px;flex:none}

  .back__brand{position:absolute;left:0;right:0;top:0;bottom:0;justify-content:center;font-size:28px}
  .back__brand .brand__dot{width:18px;height:18px}
</style>
</head>
<body>
<main class="canvas">
  <section class="card card--front" aria-label="Card front">
    <div class="brand front__brand"><span class="brand__dot"></span>Meridan Care Partners</div>
    <div class="front__rule"></div>
    <div class="person">
      <p class="person__name">Ellis Varga</p>
      <p class="person__role">President</p>
    </div>
    <p class="address">412 Alder Crescent<br>Halden Bay, Canada 20318</p>
    <ul class="contacts">
      <li><svg viewBox="0 0 12 12"><path d="M2.5 1l2 2.2-1 1.3a6 6 0 0 0 4 4l1.3-1 2.2 2-1.5 1.5C5 11 1 7 1 2.5z" fill="var(--brand-blue)"/></svg>555-210-4471</li>
      <li><svg viewBox="0 0 12 12"><rect x="3" y="1" width="6" height="10" rx="1" fill="none" stroke="var(--brand-blue)" stroke-width="1.3"/></svg>555-210-4486</li>
      <li><svg viewBox="0 0 12 12"><rect x="1" y="2.5" width="10" height="7" fill="var(--brand-blue)"/><path d="M1 2.5l5 4 5-4" fill="none" stroke="var(--card-dark)" stroke-width="1"/></svg>hello@meridancare.com</li>
      <li><svg viewBox="0 0 12 12"><circle cx="6" cy="6" r="5" fill="none" stroke="var(--brand-blue)" stroke-width="1.3"/><path d="M1 6h10M6 1c-2.5 3-2.5 7 0 10M6 1c2.5 3 2.5 7 0 10" fill="none" stroke="var(--brand-blue)" stroke-width="1"/></svg>www.meridancare.com</li>
    </ul>
  </section>

  <section class="card card--back" aria-label="Card back">
    <div class="brand back__brand"><span class="brand__dot"></span>Meridan Care Partners</div>
  </section>
</main>
</body>
</html>
```